Private Investigation Business Card Design

I need a business card for a new private investigation company named Brisk Inquiries. I perform mainly surveillance jobs, vehicle repossessions, document serves etc. The final design should aim for a professional look. The logo has a magnifying glass with stick man arms and legs and is in a running action to show the "Brisk" aspect of the name. If the colour scheme could remain the same as the website www.briskinquiries-demo.com.au with silvers,blacks and a couple electric blue highlights.
Industry/Entity Type
Business
Contact Information for Business Card
Morgan Kellaway
Brisk Inquiries
0487316204
PO Box 58, Carnwell NSW 2291
info@briskinquiries-demo.com.au
www.briskinquiries-demo.com.au
Look and feel

```html
<!DOCTYPE html>
<html lang="en">
<head>
<meta charset="utf-8">
<title>Brisk Inquiries – Business Card</title>
<link rel="stylesheet" href="https://fonts.googleapis.com/css2?family=Open+Sans:ital,wght@0,400;0,600;1,400&display=swap">
<style>
  :root {
    --backdrop: #3b3b3b;
    --card-white: #f7f7f7;
    --ink: #222222;
    --ink-soft: #4a4a4a;
    --rule: #b9b9b9;
    --band-dark: #2a2a2a;
    --silver-light: #d4d4d4;
    --silver-mid: #a9a9a9;
    --silver-dark: #8a8a8a;
    --brand-grey: #5c5c5c;
  }
  * { margin: 0; padding: 0; box-sizing: border-box; }
  html, body { width: 1200px; height: 750px; overflow: hidden; }
  body {
    background: var(--backdrop);
    font-family: "Open Sans", sans-serif;
    position: relative;
  }
  .card {
    position: absolute;
    top: 228px;
    width: 461px;
    height: 263px;
    overflow: hidden;
  }
  /* Front */
  .card-front {
    left: 124px;
    background: var(--card-white);
  }
  .brand {
    position: absolute;
    left: 34px;
    top: 102px;
    display: flex;
    align-items: center;
    gap: 10px;
  }
  .brand-name {
    font-weight: 600;
    font-size: 24px;
    color: var(--brand-grey);
    letter-spacing: 0.5px;
  }
  .brand-dot {
    width: 14px;
    height: 14px;
    border-radius: 50%;
    background: var(--brand-grey);
  }
  .divider {
    position: absolute;
    left: 231px;
    top: 66px;
    width: 1px;
    height: 108px;
    background: var(--rule);
  }
  .details {
    position: absolute;
    left: 252px;
    top: 60px;
    color: var(--ink-soft);
    font-size: 11px;
    line-height: 14px;
  }
  .holder-name {
    font-size: 16px;
    font-weight: 600;
    color: var(--ink);
    line-height: 20px;
    margin-bottom: 9px;
  }
  .address { margin-bottom: 7px; }
  .contact-line {
    display: flex;
    align-items: center;
    gap: 6px;
    height: 17.5px;
  }
  .contact-line svg { width: 11px; height: 11px; flex: none; }
  .base-rule {
    position: absolute;
    left: 0; right: 0;
    top: 241px;
    height: 2px;
    background: var(--band-dark);
  }
  .base-band {
    position: absolute;
    left: 0; right: 0;
    top: 244px;
    bottom: 0;
    background: linear-gradient(90deg, var(--silver-dark), var(--silver-light) 50%, var(--silver-dark));
  }
  /* Back */
  .card-back {
    left: 618px;
    background: radial-gradient(ellipse at 40% 45%, #d8d8d8 0%, #b8b8b8 55%, #9e9e9e 100%);
  }
  .back-figure-area {
    position: absolute;
    left: 200px;
    top: 20px;
    width: 240px;
    height: 240px;
  }
  .back-brand {
    position: absolute;
    left: 36px;
    top: 188px;
    font-weight: 600;
    font-size: 26px;
    color: var(--brand-grey);
    letter-spacing: 0.5px;
    line-height: 30px;
  }
  .back-url {
    position: absolute;
    left: 36px;
    top: 229px;
    font-style: italic;
    font-size: 10.5px;
    color: var(--ink-soft);
  }
</style>
</head>
<body>
  <section class="card card-front">
    <div class="brand">
      <span class="brand-name">Brisk Inquiries</span>
      <span class="brand-dot"></span>
    </div>
    <div class="divider"></div>
    <div class="details">
      <p class="holder-name">Morgan Kellaway</p>
      <p class="address">PO Box 58<br>Carnwell NSW 2291</p>
      <p class="contact-line">
        <svg viewBox="0 0 12 12"><path fill="#222" d="M2.4 0.6l2 2.2-1 1.3c.7 1.6 2 2.9 3.6 3.6l1.3-1 2.2 2-1.1 1.9C5 10.4 1.6 7 .5 1.7z"/></svg>
        0487 316 204
      </p>
      <p class="contact-line">
        <svg viewBox="0 0 12 12"><rect x="0.5" y="2.5" width="11" height="7.5" fill="#222"/><path d="M0.8 2.8L6 6.8l5.2-4" stroke="#f7f7f7" stroke-width="1" fill="none"/></svg>
        info@briskinquiries-demo.com.au
      </p>
      <p class="contact-line">
        <svg viewBox="0 0 12 12"><circle cx="6" cy="6" r="5.5" fill="#222"/><path d="M3 3.5c1 .3 1.5 1 1.2 2 .8.4 1 1.2.6 2.2M7.5 2c-.4.9 0 1.6 1 1.8.6 1 .3 2-.5 2.6" stroke="#f7f7f7" stroke-width=".9" fill="none"/></svg>
        www.briskinquiries-demo.com.au
      </p>
    </div>
    <div class="base-rule"></div>
    <div class="base-band"></div>
  </section>

  <section class="card card-back">
    <svg class="back-figure-area" role="img" aria-label="Faint brand figure area" viewBox="0 0 240 240">
      <defs>
        <radialGradient id="figureGlow" cx="50%" cy="45%" r="50%">
          <stop offset="0%" stop-color="#c4c4c4" stop-opacity="0.6"/>
          <stop offset="100%" stop-color="#b0b0b0" stop-opacity="0"/>
        </radialGradient>
      </defs>
      <rect width="240" height="240" fill="url(#figureGlow)"/>
    </svg>
    <p class="back-brand">Brisk Inquiries</p>
    <p class="back-url">www.briskinquiries-demo.com.au</p>
  </section>
</body>
</html>
```